Duct Manufacturing Company new to the industry needs business card and stationary design

we are sheet metal duct manufacturers looking for a business card design to fit my new business logo.
nothing to crazy that will date, but want it to stand out from the crowed.
I'm sure you guys will work it out.

Contact Information for Business Card

Glen Marsh
Director

Address
17 Dorwell St
Kelvara NSW 2581

0438 760 514

Sales@flowbend.com.au

Font styles to use
Other font styles liked:
• BankGothic md bt

Requirements
Nice to have
• Like the idea of corner rounded to match logo
• like to keep colours flowing
• font I like sharp square not rounded

```html
<!DOCTYPE html>
<html lang="en">
<head>
<meta charset="utf-8">
<title>Flowbend Industries – Business Card</title>
<link rel="stylesheet" href="https://fonts.googleapis.com/css2?family=Michroma&display=swap">
<style>
  :root {
    --backdrop: #e8e6e2;
    --card-white: #fbfbfb;
    --brand-blue-light: #1db4e8;
    --brand-blue-deep: #0b6db6;
    --accent-green: #8cc63f;
    --ink-white: #ffffff;
    --card-font: "Michroma", sans-serif;
  }
  html, body {
    margin: 0;
    padding: 0;
    width: 1200px;
    height: 780px;
    overflow: hidden;
    background: var(--backdrop);
  }
  .canvas {
    position: relative;
    width: 1200px;
    height: 780px;
  }
  .business-card {
    position: absolute;
    left: 100px;
    top: 90px;
    width: 1000px;
    height: 600px;
    border-radius: 18px;
    overflow: hidden;
    background: var(--card-white);
    box-shadow: 0 10px 30px rgba(0,0,0,0.18);
    font-family: var(--card-font);
  }
  .card-shapes {
    position: absolute;
    inset: 0;
  }
  .brand-block {
    position: absolute;
    left: 70px;
    top: 250px;
    display: flex;
    align-items: center;
    gap: 22px;
  }
  .brand-dot {
    width: 58px;
    height: 58px;
    border-radius: 50%;
    background: var(--brand-blue-deep);
    flex: none;
  }
  .brand-name {
    margin: 0;
    color: var(--brand-blue-deep);
    font-weight: 400;
    font-size: 34px;
    line-height: 1.25;
    letter-spacing: 1px;
    text-transform: uppercase;
  }
  .contact-block {
    position: absolute;
    right: 60px;
    top: 90px;
    width: 420px;
    color: var(--ink-white);
    text-align: right;
    text-transform: uppercase;
  }
  .person-name {
    margin: 0;
    font-size: 30px;
    font-weight: 400;
    letter-spacing: 2px;
  }
  .person-role {
    margin: 4px 0 46px;
    font-size: 15px;
    letter-spacing: 3px;
  }
  .contact-line {
    margin: 0 0 16px;
    font-size: 17px;
    letter-spacing: 1.5px;
    display: flex;
    justify-content: flex-end;
    align-items: center;
    gap: 12px;
  }
  .contact-line.email { text-transform: none; }
  .contact-icon {
    width: 22px;
    height: 22px;
    flex: none;
  }
</style>
</head>
<body>
<main class="canvas">
  <article class="business-card">
    <svg class="card-shapes" width="1000" height="600" viewBox="0 0 1000 600" aria-hidden="true">
      <defs>
        <linearGradient id="blueFlow" x1="0" y1="0" x2="1" y2="1">
          <stop offset="0" stop-color="#1db4e8"/>
          <stop offset="1" stop-color="#0b6db6"/>
        </linearGradient>
      </defs>
      <polygon class="blue-panel" points="640,0 1000,0 1000,600 470,600" fill="url(#blueFlow)"/>
      <line class="green-rule" x1="604" y1="0" x2="434" y2="600" stroke="#8cc63f" stroke-width="2.5"/>
    </svg>

    <div class="brand-block">
      <span class="brand-dot"></span>
      <h1 class="brand-name">Flowbend<br>Industries</h1>
    </div>

    <section class="contact-block">
      <h2 class="person-name">Glen Marsh</h2>
      <p class="person-role">Director</p>
      <p class="contact-line">17 Dorwell St</p>
      <p class="contact-line">Kelvara NSW 2581</p>
      <p class="contact-line">0438 760 514
        <svg class="contact-icon" viewBox="0 0 22 22" aria-hidden="true">
          <rect width="22" height="22" rx="3" fill="#ffffff"/>
          <path d="M7 5 L9.5 5 L10.5 8.5 L9 9.8 Q10.5 12.8 12.2 13.6 L13.5 12.2 L17 13.2 L17 15.8 Q16.6 17 15 17 Q6 16 5 7 Q5 5.3 7 5 Z" fill="#0b6db6"/>
        </svg>
      </p>
      <p class="contact-line email">Sales@flowbend.com.au
        <svg class="contact-icon" viewBox="0 0 22 22" aria-hidden="true">
          <rect width="22" height="22" rx="3" fill="#ffffff"/>
          <rect x="4" y="6" width="14" height="10" fill="none" stroke="#0b6db6" stroke-width="1.6"/>
          <path d="M4 6 L11 12 L18 6" fill="none" stroke="#0b6db6" stroke-width="1.6"/>
        </svg>
      </p>
    </section>
  </article>
</main>
</body>
</html>
```